Business cards for veterinary clinic

Hi, We are looking for business cards to be designed for our other veterinary clinic. We were very happy with the design done for our other clinic a few months ago. We already have a logo for use which I will attach (please use the image not the text around.
We need a couple of different cards (same design with different names on them) produced

Industry/Entity Type

Veterinary

Contact Information for Business Card

Bellwood Creek Vet Clinic
47 Orchard Rd
Kangaroo Flat
VIC 3555
03) 5182 6390
clinic@bellwoodcreekvetclinic.com.au

Font styles to use
Sans Serif

Colors
0455a3
0592cd

Requirements
Must have
• Three different names
• 1. Generic (no name) with email clinic@bellwoodcreekvetclinic.com.au
• 2. Hollis Varne -Director with email hollis@bellwoodcreekvetclinic.com.au
• 3. Dorian Pike - Vet Director with email hollis@bellwoodcreekvetclinic.com.au

```html
<!DOCTYPE html>
<html lang="en">
<head>
<meta charset="utf-8">
<title>Bellwood Creek Veterinary Clinic – Business Cards</title>
<link rel="stylesheet" href="https://fonts.googleapis.com/css2?family=Lato:wght@400;700;900&display=swap">
<style>
  :root {
    --backdrop: #2e2e2e;
    --sky: #55bedf;
    --sky-soft: #6ccbe6;
    --ocean: #1d86b8;
    --ocean-deep: #0f6d9e;
    --band: #2a93c4;
    --navy: #0b3f6e;
    --ink-light: #e6f5fb;
    --emblem: #eef3f6;
    --emblem-ring: #ffffff;
  }
  * { box-sizing: border-box; margin: 0; padding: 0; }
  html, body {
    width: 1200px; height: 997px; overflow: hidden;
    background: var(--backdrop);
    font-family: "Lato", Arial, sans-serif;
  }
  .stage { position: relative; width: 1200px; height: 997px; }

  .card {
    position: absolute;
    width: 620px; height: 354px;
    overflow: hidden;
    box-shadow: 0 14px 30px rgba(0,0,0,.45);
  }

  /* brand mark: plain circle with the clinic name set inside */
  .brand {
    position: absolute;
    display: flex; align-items: center; justify-content: center;
    border-radius: 50%;
    background: var(--emblem);
    border: 5px solid var(--emblem-ring);
    color: var(--navy); font-weight: 700; font-size: 18px;
    text-align: center; line-height: 1.2;
  }

  /* back of card */
  .card--back {
    left: 70px; top: 70px;
    background: linear-gradient(180deg, var(--sky-soft), var(--sky));
  }
  .card--back .web-band {
    position: absolute; left: 0; right: 0; top: 158px; height: 40px;
    background: var(--band);
    display: flex; align-items: center; padding-left: 40px;
    color: var(--ink-light); font-weight: 700; font-size: 15px; letter-spacing: .3px;
  }
  .card--back .brand { left: 400px; top: 96px; width: 166px; height: 166px; }

  /* front of card */
  .card--front {
    left: 510px; top: 560px;
    background: linear-gradient(180deg, var(--ocean) 0%, var(--ocean-deep) 100%);
  }
  .card--front .top-panel {
    position: absolute; left: 0; right: 0; top: 0; height: 150px;
    background: linear-gradient(180deg, var(--sky-soft), var(--sky));
    clip-path: polygon(0 0, 100% 0, 100% 62%, 0 100%);
  }
  .card--front .brand { left: 46px; top: 70px; width: 170px; height: 170px; }

  .clinic {
    position: absolute; right: 34px; top: 88px; text-align: right;
  }
  .clinic-name { color: var(--navy); font-weight: 700; font-size: 19px; }
  .clinic-address { color: var(--ink-light); font-weight: 700; font-size: 13px; margin-top: 3px; }

  .contact {
    position: absolute; right: 34px; top: 166px; text-align: right;
    color: var(--ink-light); font-size: 14px; list-style: none;
  }
  .contact li { display: flex; justify-content: flex-end; align-items: center; gap: 10px; height: 26px; }
  .contact li.email { margin-top: 24px; }
  .contact svg { width: 16px; height: 16px; }

  .person { position: absolute; left: 40px; top: 262px; }
  .person-name { color: var(--navy); font-weight: 900; font-size: 24px; letter-spacing: .5px; text-transform: uppercase; }
  .person-role { color: var(--navy); font-weight: 900; font-size: 14px; text-transform: uppercase; text-align: right; margin-top: 1px; }
  .pointer { position: absolute; left: 0; top: 276px; width: 14px; height: 20px; }
</style>
</head>
<body>
<main class="stage">

  <section class="card card--back" aria-label="Business card back">
    <div class="web-band">www.bellwoodcreekvetclinic.com.au</div>
    <div class="brand">Bellwood<br>Creek</div>
  </section>

  <section class="card card--front" aria-label="Business card front">
    <div class="top-panel"></div>
    <div class="brand">Bellwood<br>Creek</div>

    <div class="clinic">
      <p class="clinic-name">Bellwood Creek Veterinary Clinic</p>
      <p class="clinic-address">47 Orchard Rd Maplevale VIC 3871</p>
    </div>

    <ul class="contact">
      <li class="phone">(03) 5182 6390
        <svg viewBox="0 0 16 16" aria-hidden="true"><path fill="var(--navy)" d="M2 5c0-2 2-3 6-3s6 1 6 3v1h-3V5H5v1H2zM4 7h8l2 6H2zm4 1.5a2 2 0 1 0 0 4 2 2 0 0 0 0-4z"/></svg>
      </li>
      <li class="email">clinic@bellwoodcreekvetclinic.com.au
        <svg viewBox="0 0 16 16" aria-hidden="true"><rect x="1" y="3" width="14" height="10" fill="var(--navy)"/><path d="M1 3l7 6 7-6" fill="none" stroke="var(--ink-light)" stroke-width="1"/></svg>
      </li>
    </ul>

    <svg class="pointer" viewBox="0 0 14 20" aria-hidden="true"><path d="M0 0l14 10L0 20z" fill="#ffffff"/></svg>
    <div class="person">
      <p class="person-name">Dorian Pike</p>
      <p class="person-role">Vet Director</p>
    </div>
  </section>

</main>
</body>
</html>
```